Tri-Fold Brochure for Christian Author and Speaker

Lorna Whitfield is an inspirational author and speaker, sharing her testimony and encouraging others in their walk with Christ. A gifted writer, her work has been featured on Gently Radiant, Steadfast Mornings, and Hymns & Teacups Magazine (Fall 2011).

Lorna ‘s first book, Leaving the Lantern Room: Unmasking Hidden Snares in Ordinary Living, is an informative memoir and Bible study, recounting her journey from committed Christian to witch, medium, and ghost hunter for eight years until restored to faith in Jesus Christ. She was a contributing author to Walking Past the Shadows: A Candid View of Sorcery from Those Who Left by Dale Pennington and a consultant for the novel The Keeper of Marlow Hollow by Beacon Prize Winning Author, Helen Osgood.

Lorna’s second book, An Insider’s Guide to Spiritual Warfare: 20 Battle-Tested Strategies from Behind Enemy Lines, will be published by Harvest Lane Press for Fall 2014.

Lorna is a wife and mother. She enjoys writing, spending time with her family, taking long walks, listening to music of all kinds, and experiencing God’s daily gift called life.

You can read more about Lorna and see the look and feel we are going for at www.lornawhitfield.example

The brochure is to be used as a promotional tool to gain Lorna speaking engagements. You can see the topics she covers at http://www.lornawhitfield.example/speaking-engagements/.

More info can be found at: https://www.facebook.com/AuthorLornaWhitfield
https://www.facebook.com/VMUCX
https://www.facebook.com/LeavingtheLanternRoom
https://www.facebook.com/OpenDoorOutreach
http://www.opendooroutreach.example

I have uploaded 3 headshots, book covers for both of Lorna's books and the design layout in .EPS format from Swiftprintery.example where I will be getting printing done.

3 more days till the contest ends get your final designs in.

Reason: I'm extending this as I am tied up at a leadership conference and will not be able to give this the attention it deserves till the weekend.

Target Market(s)

Churches and women's groups. Lorna's current audience skews heavy to women on a 70/30 ratio.

Industry/Entity Type

Christian

Requirements
Must have
• Headshot I have uploaded 3
Quotes from previous speaking engagements you can find those at http://www.lornawhitfield.example/speaking-engagements/

```html
<!DOCTYPE html>
<html lang="en">
<head>
<meta charset="utf-8">
<title>Lorna Whitfield – Author | Speaker Brochure</title>
<link href="https://fonts.googleapis.com/css2?family=Cinzel:wght@400;600&family=Questrial&family=Fredoka:wght@500;600&display=swap" rel="stylesheet">
<style>
  :root{
    --crimson:#a8174f;
    --crimson-dark:#8c1040;
    --blush:#f7eef0;
    --cream:#fbf6f2;
    --ink:#4a3a40;
    --stage:#e8e8ea;
    --white:#ffffff;
  }
  *{box-sizing:border-box;margin:0;padding:0}
  html,body{width:1200px;height:800px;overflow:hidden;background:var(--stage)}
  .canvas{position:relative;width:1200px;height:800px}
  .page{position:absolute;background:linear-gradient(160deg,var(--cream),var(--blush));overflow:hidden;font-family:"Questrial",sans-serif;color:var(--ink)}
  .band{position:absolute;left:0;width:100%}

  /* spread */
  .page--left{left:40px;top:150px;width:340px;height:470px}
  .page--right{left:380px;top:150px;width:340px;height:470px}
  .spread-fold{position:absolute;left:379px;top:150px;width:2px;height:470px;background:rgba(0,0,0,.08)}

  .section-tab{position:absolute;left:14px;top:30px;background:var(--white);border:2px solid var(--crimson);border-radius:10px 10px 10px 0;padding:3px 16px;font-family:"Fredoka",sans-serif;font-weight:500;font-size:24px;color:var(--crimson)}
  .intro{position:absolute;left:150px;top:28px;width:176px;font-size:7px;line-height:1.45}
  .lead-line{position:absolute;left:14px;top:80px;width:180px;font-size:8px;line-height:1.4}
  .lead-line b{color:var(--crimson)}
  .headshot{position:absolute;left:218px;top:74px;width:56px;height:70px;border:2px solid var(--white);background:linear-gradient(170deg,#6b5a4c,#8a5a3c 45%,#c9b8a6)}
  .topics{position:absolute;left:26px;top:112px;font-family:"Fredoka",sans-serif;font-weight:500;font-size:9px;color:var(--crimson);line-height:1.45}
  .topics h3{font-size:10px;font-weight:600}
  .topics ul{padding-left:12px}
  .speaker-q{position:absolute;left:14px;top:218px;width:190px;font-family:"Fredoka",sans-serif;font-weight:600;font-size:14px;line-height:1.15;color:var(--crimson)}
  .quote{position:absolute;font-size:7px;line-height:1.5}
  .quote h4{font-family:"Fredoka",sans-serif;font-weight:500;font-size:10px;line-height:1.2;color:var(--crimson);margin-bottom:4px}
  .quote--a{left:14px;top:260px;width:140px}
  .quote--a p{font-size:8.5px}
  .quote--b{left:168px;top:220px;width:158px}

  .page-title{position:absolute;right:18px;top:8px;width:110px;font-family:"Cinzel",serif;font-weight:400;font-size:15px;line-height:1.05;color:var(--white);text-align:center}
  .page-title small{display:block;font-size:10px;line-height:1.1}
  .quote--c{left:12px;top:14px;width:138px}
  .quote--d{left:12px;top:126px;width:70px}
  .quote--e{left:86px;top:126px;width:160px}
  .quote--f{left:12px;top:240px;width:150px}
  .quote--g{left:258px;top:250px;width:76px}

  /* cover */
  .page--cover{left:760px;top:110px;width:400px;height:540px;box-shadow:0 2px 6px rgba(0,0,0,.12)}
  .cover-name{position:absolute;left:0;right:0;top:26px;text-align:center;font-family:"Cinzel",serif;font-weight:400;font-size:34px;color:var(--crimson);letter-spacing:1px}
  .cover-role{position:absolute;right:36px;top:72px;font-family:"Cinzel",serif;font-size:15px;color:var(--crimson);letter-spacing:1px}
  .cover-photo{position:absolute;left:0;top:108px;width:400px;height:320px}
  .cover-tagline{position:absolute;left:70px;top:440px;font-family:"Fredoka",sans-serif;font-weight:600;color:var(--crimson);font-size:25px;line-height:1.05}
  .cover-tagline span{display:block}
  .cover-tagline .is{font-size:20px}
  .cover-tagline .indent{padding-left:72px}
  .cover-tagline .indent2{padding-left:110px}
</style>
</head>
<body>
<main class="canvas">

  <!-- inside spread, left page -->
  <section class="page page--left">
    <svg class="band" style="top:0;height:60px" viewBox="0 0 340 60" preserveAspectRatio="none" aria-hidden="true">
      <path d="M0 0H340V14C250 10 170 30 0 26Z" fill="var(--crimson)"/>
    </svg>
    <svg class="band" style="bottom:0;height:40px" viewBox="0 0 340 40" preserveAspectRatio="none" aria-hidden="true">
      <path d="M0 22C120 8 240 30 340 14V40H0Z" fill="var(--crimson)"/>
    </svg>
    <div class="section-tab">Speaking</div>
    <p class="intro">As a speaker, Lorna Whitfield draws from her own life lessons and a Biblical foundation, encouraging others toward a deeper walk with Christ through honest stories and practical teaching.</p>
    <p class="lead-line">God, Lorna offers sound, heartfelt, and practical biblical advice on issues relevant to today's <b>Modern Day Believer</b>, read more…</p>
    <div class="headshot" role="img" aria-label="Headshot photograph of Lorna Whitfield"></div>
    <div class="topics">
      <h3>Speaking Topics Include:</h3>
      <ul>
        <li>Christians and the Occult</li>
        <li>Homelessness (with Tom Whitfield)</li>
        <li>Human Trafficking</li>
        <li>Marriage Restoration (with Tom Whitfield)</li>
        <li>Prayer as a Lifestyle</li>
        <li>Spiritual Warfare</li>
      </ul>
    </div>
    <h2 class="speaker-q">What's Lorna Like as A Speaker?</h2>
    <div class="quote quote--a">
      <h4>Maren Holloway, Cedar Rise Community Church Women's Ministry:</h4>
      <p>The Women's Ministry at Cedar Rise Church in Ashford, MI invited Lorna Whitfield to our Mother &amp; Daughter Banquet earlier this month. I am so glad she accepted! We couldn't have chosen a better speaker. Lorna took our theme and wove it into her talk, read more…</p>
    </div>
    <div class="quote quote--b">
      <h4>Trent Calloway, Kindred Crossing Seminar Teen Coordinator:</h4>
      <p>“I was honored and delighted to have Lorna Whitfield as one of our speakers at the Kindred Crossing Teen Seminar in Harlow Bay, Michigan. Lorna has a warm testimony and style of speaking that keeps people, young and old, engaged. Her stories of involvement in the occult and her conclusion of how God rescued her drew many of the questions that people often have. read more…</p>
    </div>
  </section>

  <!-- inside spread, right page -->
  <section class="page page--right">
    <svg class="band" style="top:0;height:72px" viewBox="0 0 340 72" preserveAspectRatio="none" aria-hidden="true">
      <path d="M150 0H340V70C300 64 250 64 205 52C178 44 158 24 150 0Z" fill="var(--crimson)"/>
    </svg>
    <svg class="band" style="bottom:0;height:30px" viewBox="0 0 340 30" preserveAspectRatio="none" aria-hidden="true">
      <path d="M0 16C120 4 240 24 340 10V30H0Z" fill="var(--crimson)"/>
    </svg>
    <h2 class="page-title">Author<small>&amp;</small>Speaker</h2>
    <div class="quote quote--c">
      <h4>Joan Pelham, Lamplight Covenant Church, Women's Christmas Tea Coordinator</h4>
      <p>“We had Lorna speak at our Women's Tea. Even though the weather was terrible we had a good turnout and several women told me afterwards how blessed they were by Lorna's message, read more…</p>
    </div>
    <div class="quote quote--d">
      <h4>Gerrit Vandermolen, Pastor, Mercy Reformed Church</h4>
      <p>Lorna brought our church a clear and caring word.</p>
    </div>
    <div class="quote quote--e">
      <p>“Lorna Whitfield spoke at our church, sharing with us her testimony, which includes how she attempted to blend witchcraft with Christianity. Obviously, she discovered there is no compromising of the Gospel, and there is a spiritual hunger in many that the Word of God alone satisfies. Her talk was honest and grace filled, read more…</p>
    </div>
    <div class="quote quote--f">
      <h4>Wes Dunmore, Youth Director, Crossroads Harbor Church</h4>
      <p>“I invited Lorna to come to the youth group that I pastor to share her testimony. She was real and open, and she showed our students how powerful God's grace is in a life that seemed lost. She made sure the students knew that witchcraft is not something to mess with, read more…</p>
    </div>
    <div class="quote quote--g">
      <h4>Celeste Marlowe, Founder, Joyful Motion Fitness</h4>
      <p>“Lorna's unique testimony and remarkable message are a gift to any group, read more…</p>
    </div>
  </section>
  <div class="spread-fold" aria-hidden="true"></div>

  <!-- front cover -->
  <section class="page page--cover">
    <h1 class="cover-name">LORNA WHITFIELD</h1>
    <p class="cover-role">AUTHOR | SPEAKER</p>
    <svg class="cover-photo" viewBox="0 0 400 320" preserveAspectRatio="none">
      <defs>
        <linearGradient id="photoTone" x1="0" y1="0" x2="1" y2="1">
          <stop offset="0" stop-color="#5f6b3e"/>
          <stop offset=".45" stop-color="#7a5a48"/>
          <stop offset="1" stop-color="#c9b3a3"/>
        </linearGradient>
      </defs>
      <path d="M0 40C120 0 260 0 400 14V300C260 320 120 300 0 270Z" fill="url(#photoTone)" role="img" aria-label="Portrait photograph of Lorna Whitfield in a garden"/>
      <path d="M0 40C120 0 260 0 400 14V4C260 -8 120 -6 0 26Z" fill="var(--crimson)"/>
      <path d="M0 270C120 300 260 320 400 300V320H0Z" fill="var(--crimson)"/>
    </svg>
    <p class="cover-tagline">
      <span>Lorna Whitfield</span>
      <span class="is indent">is an Inspirational</span>
      <span class="indent">Author</span>
      <span class="indent2">and Speaker</span>
    </p>
  </section>

</main>
</body>
</html>
```